Brookvane Consulting Business Card Design

Business Card Design for Brookvane Consulting. Brookvane Consulting is a boutique consultancy based in Atlanta, GA., that specializes in marketing strategy, organization planning, and leadership development. We provide solutions for small businesses and startups as well as Vantage 300 companies.

http://brookvaneconsulting.com/

Target Market(s)

We provide solutions for small businesses and startups as well as Vantage 300 companies.

Industry/Entity Type

Consulting

Contact Information for Business Card

Two sided business card with priority on contact information, logo, tag line (Inspiration to Dream More, Do More, Become More)

Colors

Designer to choose colors to be used in the design.

Requirements
Must have
• contact information, logo, tag line (Inspiration to Dream More, Do More, Become More)
• Simple no over communication.
Nice to have
• I would like to see different placements of logo and creative use of both sides of the card
Should not have
• Do not put too much information on the card.

```html
<!DOCTYPE html>
<html lang="en">
<head>
<meta charset="utf-8">
<title>Brookvane Consulting – Business Card</title>
<link href="https://fonts.googleapis.com/css2?family=Roboto:wght@400;500;700&display=swap" rel="stylesheet">
<style>
  :root {
    --backdrop: #4a4a4a;
    --card: #3a3a3a;
    --ink-dark: #1c1c1c;
    --ink-light: #ffffff;
    --band-grey: #8e8e8e;
    --band-mid: #2b2b2b;
    --band-pale: #b8b8b8;
    --band-black: #0d0d0d;
  }
  * { margin: 0; padding: 0; box-sizing: border-box; }
  html, body { width: 799px; height: 1200px; overflow: hidden; }
  body {
    background: var(--backdrop);
    font-family: "Roboto", Arial, sans-serif;
    position: relative;
  }
  .card {
    position: absolute;
    left: 80px;
    width: 640px;
    height: 366px;
    border-radius: 22px;
    background: var(--card);
    overflow: hidden;
    box-shadow: 0 12px 30px rgba(0,0,0,0.35);
  }
  .card--front { top: 110px; }
  .card--back { top: 720px; }

  .front-logo {
    position: absolute;
    inset: 0;
    display: flex;
    align-items: center;
    justify-content: center;
    gap: 16px;
    color: var(--ink-dark);
  }
  .logo-mark {
    width: 30px; height: 30px;
    background: currentColor;
  }
  .logo-name {
    font-weight: 700;
    font-size: 46px;
    letter-spacing: 0.5px;
  }

  .back-logo {
    position: absolute;
    left: 34px; top: 36px;
    display: flex;
    align-items: center;
    gap: 12px;
    color: var(--ink-light);
  }
  .back-logo .logo-mark { width: 22px; height: 22px; }
  .back-logo .logo-name { font-size: 32px; }

  .contact {
    position: absolute;
    left: 34px; top: 110px;
    color: var(--ink-light);
  }
  .contact__name { font-weight: 700; font-size: 22px; margin-bottom: 10px; }
  .contact__line { font-size: 15px; line-height: 20px; }

  .wave { position: absolute; left: 0; top: 0; width: 640px; height: 366px; }

  .tagline {
    position: absolute;
    right: 34px; bottom: 26px;
    text-align: right;
    color: var(--ink-light);
    font-size: 17px;
    line-height: 22px;
  }
</style>
</head>
<body>
  <section class="card card--front" aria-label="Card front">
    <div class="front-logo">
      <span class="logo-mark"></span>
      <span class="logo-name">Brookvane Consulting</span>
    </div>
  </section>

  <section class="card card--back" aria-label="Card back">
    <svg class="wave" viewBox="0 0 640 366" aria-hidden="true">
      <path d="M0,205 C150,300 390,255 640,225 L640,366 L0,366 Z" fill="var(--band-grey)"/>
      <path d="M0,218 C150,318 390,272 640,240 L640,366 L0,366 Z" fill="var(--band-mid)"/>
      <path d="M0,240 C160,330 400,284 640,250 L640,366 L0,366 Z" fill="var(--band-pale)"/>
      <path d="M0,250 C160,340 400,294 640,258 L640,366 L0,366 Z" fill="var(--band-black)"/>
    </svg>
    <div class="back-logo">
      <span class="logo-mark"></span>
      <span class="logo-name">Brookvane Consulting</span>
    </div>
    <div class="contact">
      <p class="contact__name">Dorian</p>
      <p class="contact__line">404-555-0172</p>
      <p class="contact__line">dorian@brookvaneconsulting.com</p>
      <p class="contact__line">www.brookvaneconsulting.com</p>
    </div>
    <p class="tagline">Inspiration to<br>Dream More,<br>Do More,<br>Become More</p>
  </section>
</body>
</html>
```